Meadowfield Baptist Church Banner Design

Designing 6 banners (3 + 3 that will hang on opposite sides of our auditorium) that are 10 feet long by 4 feet wide.

Use our branding guide - specifically item 4 (vertical logo) and item 5 (icon logo).

Design elements found in our KINDLE booklet, we would like to see designs that utilize the white, green and blue colour palettes but NOT the grey. Other colours may be incorporated (e.g. coral).

We are looking for 3 banner designs that would match on either side of the auditorium, the first banner incorporating the word "TRUTH", the second incorporating the word "LOVE", and the third incorporating the word "MISSION".

We interested in incorporating graphics such as trees or outdoor themes.

Font styles to use
Other font styles liked:
• Montserrat

Colors
34a7d7
00a990
f47c35

Requirements
Must have
• Banner Type #1 include the word "TRUTH"
Banner Type #2 include the word "LOVE"
Banner Type #3 include the word "MISSION"

Colour scheme must include CMYK 54 / 5 / 16 / 0 (which is available in the branding guide.) We have selected the three colours, included below in the brief.

From the branding guide - utilize #5 (icon) for the banner.

UPDATE: After reviewing the initial submissions, we are asking for designs that ONLY incorporate #5 - the ICON logo for the banners.
Nice to have
• It would be nice to have some creativity with the colour ... though a more minimalistic style is preferred.

Graphic adaptations such as trees in the background would be of interest.
Should not have
• Colour scheme should not be gray scale.

The banners should NOT be too busy.

Scripture verses (written out) are not necessary.

```html
<!DOCTYPE html>
<html lang="en">
<head>
<meta charset="utf-8">
<title>Love Never Fails – Meadowfield Baptist Church Banner</title>
<link rel="stylesheet" href="https://fonts.googleapis.com/css2?family=Montserrat:wght@700;800&family=Caveat+Brush&family=Tinos:ital@1&display=swap">
<style>
  :root {
    --banner-blue: #34a7d7;
    --ink-white: #ffffff;
    --ink-black: #0d0d0d;
    --mark-tint: rgba(255, 255, 255, 0.38);
  }
  html, body {
    margin: 0;
    padding: 0;
    width: 1200px;
    height: 2953px;
    overflow: hidden;
  }
  .banner {
    position: relative;
    width: 1200px;
    height: 2953px;
    background: var(--banner-blue);
    overflow: hidden;
  }
  .headline {
    position: absolute;
    margin: 0;
    left: 0;
    top: 0;
    width: 100%;
    height: 100%;
    font-weight: normal;
  }
  .headline__love,
  .headline__fails {
    position: absolute;
    font-family: "Montserrat", sans-serif;
    font-weight: 800;
    color: var(--ink-white);
    line-height: 1;
    letter-spacing: -6px;
  }
  .headline__love {
    left: 150px;
    top: 640px;
    font-size: 330px;
  }
  .headline__never {
    position: absolute;
    left: 205px;
    top: 870px;
    font-family: "Caveat Brush", cursive;
    font-size: 300px;
    line-height: 1;
    color: var(--ink-black);
    transform: rotate(-4deg);
    transform-origin: left center;
    letter-spacing: 4px;
  }
  .headline__fails {
    left: 215px;
    top: 1190px;
    font-size: 370px;
  }
  .verse-ref {
    position: absolute;
    left: 0;
    width: 1230px;
    top: 1615px;
    margin: 0;
    text-align: center;
    font-family: "Tinos", serif;
    font-style: italic;
    font-size: 96px;
    color: var(--ink-white);
  }
  .church-name {
    position: absolute;
    left: 70px;
    bottom: 150px;
    margin: 0;
    font-family: "Montserrat", sans-serif;
    font-weight: 700;
    font-size: 78px;
    line-height: 1.1;
    color: var(--mark-tint);
  }
</style>
</head>
<body>
  <main class="banner">
    <h1 class="headline">
      <span class="headline__love">Love</span>
      <span class="headline__never">never</span>
      <span class="headline__fails">fails</span>
    </h1>
    <p class="verse-ref">1 Corinthians 13:8</p>
    <p class="church-name">Meadowfield<br>Baptist Church</p>
  </main>
</body>
</html>
```